Wordpress website for a new Podcast

Hi, We are looking for a designer to create a wordpress website project for a new podcast and publish it on the domain we own.

The show is called “Bright Gatherings” (logo included) and its aim is to interview guests who work as professional facilitators, trainers, teachers and coaches. The show has a positive vibe, is fun, vibrant and full of positive energy. These are the feelings we want to convey in the design.

The website should have a similar structure to: https://www.plumvesselcast.example/ with the following content:

1) The main page including:
- navigation bar and social buttons at the top
- main graphic design featuring the latest episode
- "latest episodes" section displaying 3 episodes (please design a mask to be used for new episodes when they air together with the face of the interviewee) -> this will link to the respective episodes
- please design an "bright gatherings" book cover mockup to be inluded as a banner -> this will link to Orindel
- subscribe to the newsletter - a banner capturing the name and email of the user -> to be connected to PostWren.
-> a working episode search.

2) Episodes page
- the show will be divided into seasons (12 episodes each) and each episode will need a separate "blog entry" including:
-> A short article (4-5 paragraphs) + stock image
-> interviewee's bio and social links

3) Meet the hosts page
- including bios of the two hosts of the show
- links to their social profiles
- a "request speaker availability" form which sends an email

Some additional nice-to-haves:
1) Good and clean Bio's would be awesome (both for the hosts & the interviewees),
2) an easily navigable episode system,
3) a keyword/date search option
4) easy to share options (share to WhatsApp, Facebook, Twitter, LinkedIn) 5) We must be able to track how the podcasts are shared (google analytics?)

```html
<!DOCTYPE html>
<html lang="en">
<head>
<meta charset="utf-8">
<title>Bright Gatherings – Podcast</title>
<link href="https://fonts.googleapis.com/css2?family=Open+Sans:wght@400;600;700&family=Raleway:wght@700;800&display=swap" rel="stylesheet">
<style>
:root{
  --orange:#f25a0a;
  --orange-2:#f7a21b;
  --navy:#2c3550;
  --ink:#1b1b1b;
  --grey:#777;
  --gold:#f3bb50;
  --gold-2:#f6c96b;
  --faint:#eeeeee;
  --black:#141414;
}
*{box-sizing:border-box;margin:0;padding:0}
html,body{width:1200px;height:2556px;overflow:hidden;background:#fff}
body{position:relative;font-family:"Open Sans",Arial,sans-serif;color:var(--ink)}
.abs{position:absolute}
.btn{position:absolute;background:var(--orange);color:#fff;font-weight:700;display:flex;align-items:center;justify-content:center;text-transform:uppercase}
.heading{font-family:"Raleway","Open Sans",sans-serif;font-weight:800;text-transform:uppercase}

/* header */
.site-header{position:absolute;left:0;top:0;width:1200px;height:98px;background:#fff;z-index:3;box-shadow:0 1px 0 #e5e5e5}
.social{position:absolute;display:flex;gap:9px}
.social span{width:31px;height:31px;border:1.5px solid #333;border-radius:50%;display:flex;align-items:center;justify-content:center;font-size:9px;font-weight:700;color:#222;letter-spacing:.2px}
.nav a{position:absolute;font-size:14px;font-weight:700;color:#111;text-decoration:none;letter-spacing:.2px}
.nav a.active{color:var(--orange)}
.nav a.active::after{content:"";position:absolute;left:0;right:0;bottom:-9px;height:4px;background:var(--orange)}
.search{position:absolute;left:852px;top:12px;width:244px;height:36px;border:1px solid #999;border-radius:3px;padding:9px 16px;font-size:14px;color:#888}
.brand{position:absolute;left:545px;top:39px;width:118px;height:118px;border-radius:50%;background:radial-gradient(circle at 50% 55%,#ffc21a,#f57f0d 70%,#ee5708);display:flex;align-items:center;justify-content:center;text-align:center;font-weight:700;color:#111;font-size:14px;line-height:1.15;z-index:4}

/* hero */
.hero{position:absolute;left:0;top:98px;width:1200px;height:640px}
.book{position:absolute;left:163px;top:87px;width:277px;height:465px;background:linear-gradient(90deg,#ececec,#f7f7f7 60%,#cfcfcf);border-radius:4px}
.hero-title{left:558px;top:172px;font-size:48px;color:#fff;letter-spacing:.5px}
.hero-text{left:558px;top:259px;width:540px;font-size:17px;line-height:27px;color:#fff;font-weight:600}
.dots{left:577px;top:578px;display:flex;gap:3px}
.dots i{width:10px;height:10px;border:1.5px solid #fff;border-radius:50%;display:block}

/* vertical labels */
.side-label{position:absolute;left:38px;font-family:"Raleway",sans-serif;font-weight:800;font-size:44px;color:var(--faint);writing-mode:vertical-rl;transform:rotate(180deg);text-transform:uppercase;white-space:nowrap}

/* episodes */
.section-title{left:0;width:1200px;text-align:center;font-size:40px}
.card{position:absolute;top:920px;width:321px;height:470px;background:#fff;box-shadow:0 0 4px rgba(0,0,0,.25)}
.card .photo{height:230px;background:linear-gradient(180deg,#d9d9d9,#c4c4c4)}
.card .badge{position:absolute;left:135px;top:207px;width:52px;height:46px}
.card .ep{position:absolute;left:28px;top:253px;font-size:16px;color:var(--grey)}
.card h3{position:absolute;left:28px;top:288px;font-size:18.5px;font-weight:600}
.card p{position:absolute;left:28px;top:324px;width:270px;font-size:14.5px;line-height:27px;color:var(--grey)}
.card .btn{left:28px;top:422px;width:101px;height:34px;font-size:14px}

/* newsletter */
.newsletter{position:absolute;left:0;top:1500px;width:1200px;height:348px;background:linear-gradient(135deg,var(--gold),var(--gold-2) 45%,var(--gold) 75%,#f1b445)}
.newsletter .side-label{color:rgba(255,255,255,.18);top:20px}
.news-title{left:0;top:101px;width:1200px;text-align:center;font-size:40px;color:#fff}
.field{position:absolute;top:187px;width:361px;height:43px;background:#fff;font-size:15px;color:#666;padding:11px 16px;display:flex;align-items:center;gap:8px}

/* about */
.about-frame{left:127px;top:1950px;width:412px;height:226px;border:2px solid #f2c200}
.video{left:111px;top:1968px;width:410px;height:225px;background:linear-gradient(90deg,#1f1f22,#4a4a4e 50%,#1e1e20)}
.about-title{left:624px;top:1950px;font-size:40px}
.about-text{left:624px;top:2011px;width:472px;font-size:14.6px;line-height:27.6px;color:var(--grey)}
.books{left:1015px;top:2170px;width:165px;height:132px;background:linear-gradient(180deg,#e9e9e9,#cfcfcf);border-radius:6px}

/* footer */
.footer-links{left:0;top:2434px;width:1200px;text-align:center;font-size:15px;color:#fff}
.footer-links span{margin:0 17px}
.contact-row{left:325px;top:2480px;display:flex;align-items:center;gap:10px;color:#fff;font-size:15px}
.contact-row .social span{border-color:#fff;color:#fff}
.copy{left:0;top:2536px;width:1200px;text-align:center;color:#fff;font-size:14px}
</style>
</head>
<body>

<header class="site-header">
  <div class="social" style="left:111px;top:14px"><span>FB</span><span>WA</span><span>TW</span><span>LI</span></div>
  <nav class="nav">
    <a class="active" style="left:111px;top:69px">HOME</a>
    <a style="left:201px;top:69px">ABOUT US</a>
    <a style="left:329px;top:69px">MEET THE HOSTS</a>
    <a style="left:760px;top:65px">EPISODES</a>
    <a style="left:883px;top:65px">SERVICES</a>
    <a style="left:1003px;top:65px">CONTACT US</a>
  </nav>
  <div class="search">Search
    <svg class="abs" style="right:16px;top:10px" width="15" height="15" viewBox="0 0 16 16"><circle cx="6.5" cy="6.5" r="5" fill="none" stroke="#111" stroke-width="2"/><line x1="10.5" y1="10.5" x2="15" y2="15" stroke="#111" stroke-width="2.4"/></svg>
  </div>
</header>
<div class="brand">BRIGHT<br>GATHERINGS</div>

<section class="hero">
  <svg class="abs" style="left:0;top:0" width="1200" height="640" viewBox="0 0 1200 640">
    <defs>
      <linearGradient id="heroBg" x1="0" y1="0" x2="1" y2="1">
        <stop offset="0" stop-color="#252d47"/><stop offset=".55" stop-color="#3a4058"/><stop offset="1" stop-color="#5a5b66"/>
      </linearGradient>
      <linearGradient id="edge" x1="0" x2="1"><stop offset="0" stop-color="#f7a21b"/><stop offset="1" stop-color="#f25a0a"/></linearGradient>
    </defs>
    <polygon points="0,0 1200,0 1200,522 604,636 0,522" fill="url(#edge)"/>
    <polygon points="0,0 1200,0 1200,512 604,624 0,512" fill="url(#heroBg)"/>
  </svg>
  <div class="book" role="img" aria-label="Bright Gatherings hardcover book mockup"></div>
  <h1 class="abs heading hero-title">Bright Gatherings</h1>
  <p class="abs hero-text">Nemo enim ipsam voluptatem quia voluptas sit aspernatur aut odit aut fugit, sed quia consequuntur</p>
  <a class="btn" style="left:558px;top:353px;width:197px;height:48px;font-size:16px">Get the book now</a>
  <div class="abs dots"><i></i><i></i><i style="background:#fff"></i><i></i><i></i></div>
</section>

<div class="side-label" style="top:875px;height:410px">Latest Episodes</div>
<h2 class="abs heading section-title" style="top:826px">Latest Podcast Episodes</h2>

<article class="card" style="left:110px">
  <div class="photo" role="img" aria-label="Portrait of episode guest on grey studio backdrop"></div>
  <svg class="badge" viewBox="0 0 52 46"><polygon points="13,0 39,0 52,23 39,46 13,46 0,23" fill="#f7a21b"/><circle cx="26" cy="22" r="9" fill="none" stroke="#fff" stroke-width="2.5"/><circle cx="26" cy="22" r="3" fill="#fff"/></svg>
  <span class="ep">Episode 201</span>
  <h3>soluta nobis est eligendi optio</h3>
  <p>Nam libero tempore,&nbsp; soluta nobis&nbsp; est eligendi optio cumque nihil quo minus id quod maxime placeat facere</p>
  <a class="btn">Explore</a>
</article>
<article class="card" style="left:443px">
  <div class="photo" role="img" aria-label="Portrait of episode guest on grey studio backdrop"></div>
  <svg class="badge" viewBox="0 0 52 46"><polygon points="13,0 39,0 52,23 39,46 13,46 0,23" fill="#f7a21b"/><circle cx="26" cy="22" r="9" fill="none" stroke="#fff" stroke-width="2.5"/><circle cx="26" cy="22" r="3" fill="#fff"/></svg>
  <span class="ep">Episode 200</span>
  <h3>soluta nobis est eligendi optio</h3>
  <p>Nam libero tempore,&nbsp; soluta nobis&nbsp; est eligendi optio cumque nihil quo minus id quod maxime placeat facere</p>
  <a class="btn">Explore</a>
</article>
<article class="card" style="left:775px">
  <div class="photo" role="img" aria-label="Two episode guests standing on grey studio backdrop"></div>
  <svg class="badge" viewBox="0 0 52 46"><polygon points="13,0 39,0 52,23 39,46 13,46 0,23" fill="#f7a21b"/><circle cx="26" cy="22" r="9" fill="none" stroke="#fff" stroke-width="2.5"/><circle cx="26" cy="22" r="3" fill="#fff"/></svg>
  <span class="ep">Episode 199</span>
  <h3>soluta nobis est eligendi optio</h3>
  <p>Nam libero tempore,&nbsp; soluta nobis&nbsp; est eligendi optio cumque nihil quo minus id quod maxime placeat facere</p>
  <a class="btn">Explore</a>
</article>

<section class="newsletter">
  <div class="side-label" style="height:320px">Newsletter</div>
  <svg class="abs" style="left:582px;top:38px" width="44" height="44" viewBox="0 0 44 44"><circle cx="22" cy="22" r="20.5" fill="none" stroke="#fff" stroke-width="2"/><rect x="13" y="16" width="18" height="13" rx="2" fill="none" stroke="#fff" stroke-width="2"/><polyline points="13,17 22,24 31,17" fill="none" stroke="#fff" stroke-width="2"/></svg>
  <h2 class="abs heading news-title">Subscribe the Newsletter</h2>
  <div class="field" style="left:231px">
    <svg width="11" height="13" viewBox="0 0 11 13"><circle cx="5.5" cy="3.5" r="3" fill="#777"/><path d="M0 13 Q0 7 5.5 7 Q11 7 11 13Z" fill="#777"/></svg>Enter Your Name</div>
  <div class="field" style="left:617px">
    <svg width="15" height="11" viewBox="0 0 15 11"><rect x="1" y="1" width="13" height="9" fill="none" stroke="#777" stroke-width="1.5"/><polyline points="1,1.5 7.5,6 14,1.5" fill="none" stroke="#777" stroke-width="1.5"/></svg>Enter Your Email</div>
  <a class="btn" style="left:538px;top:265px;width:133px;height:43px;font-size:14px">Subscribe</a>
</section>

<div class="side-label" style="top:1950px;height:245px">About Us</div>
<div class="abs about-frame"></div>
<div class="abs video" role="img" aria-label="Video still of a businessman holding a glowing interface"></div>
<svg class="abs" style="left:298px;top:2062px" width="36" height="36" viewBox="0 0 36 36"><circle cx="18" cy="18" r="18" fill="#e3221b"/><polygon points="14,11 26,18 14,25" fill="#fff"/></svg>
<h2 class="abs heading about-title">About Us</h2>
<p class="abs about-text">Nor again is there anyone who loves or pursues or desires to obtain pain of itself, because it is pain, because occasionally circumstances occur in which toil and pain can procure him some great pleasure.To take a trivial example, which of&nbsp; ever undertakes laborious physical exercise, except to obtain some advantage</p>
<a class="btn" style="left:624px;top:2165px;width:130px;height:37px;font-size:15px">Learn more</a>

<footer>
  <svg class="abs" style="left:0;top:2272px" width="1200" height="284" viewBox="0 0 1200 284"><polygon points="0,2 604,60 1200,2 1200,284 0,284" fill="var(--black)"/></svg>
  <div class="abs books" role="img" aria-label="Sketch of a stack of books"></div>
  <div class="brand" style="left:558px;top:2308px;width:94px;height:94px;font-size:11.5px">BRIGHT<br>GATHERINGS</div>
  <div class="abs footer-links">Home<span>|</span>About Us<span>|</span>Meet the hosts<span>|</span>Episodes<span>|</span>services<span>|</span>Blog<span>|</span>Contact Us</div>
  <div class="abs contact-row">
    <svg width="15" height="11" viewBox="0 0 15 11"><rect x="1" y="1" width="13" height="9" fill="none" stroke="#fff" stroke-width="1.5"/><polyline points="1,1.5 7.5,6 14,1.5" fill="none" stroke="#fff" stroke-width="1.5"/></svg>
    <span>hello@brightgatherings.example</span>
    <svg style="margin-left:18px" width="13" height="13" viewBox="0 0 14 14"><path d="M3 1 L5.5 4 L4 6 Q6 9 8 10 L10 8.5 L13 11 L11 13.5 Q2 11 0.5 3Z" fill="#fff"/></svg>
    <span>555 014 2290</span>
    <div class="social" style="position:static;margin-left:28px;gap:7px"><span>FB</span><span>WA</span><span>TW</span><span>LI</span></div>
  </div>
  <div class="abs copy">© 2019 Bright Gatherings. All Rights Reserved</div>
</footer>

</body>
</html>
```